Corporate Travel Technology Company needs new Business Card design

We need a new business card design to reflect our re-branded company. Our company is called tolvEn (pronounced tolvenn) and we provide Business Intelligence and mobile travel management solutions for the corporate travel industry. Our multinational customers use our solutions to manage large travel budgets and frequent travellers, as well as to save money and reduce risk. We'd like to see designs that use the blue and green palette as well as our corporate logo (attached below). The design should communicate innovation, insight, forward thinking, contemporary, trusted.

Target Market(s)

Large multinational corporates and Travel Agencies.

Industry/Entity Type

Business

Contact Information for Business Card

Rosalind Mercer
Chief Executive
tolvEn
Phone number - +61 (0)2 8134 2907
Email address - rosalind.mercer@tolven-example.com
Mobile number - +61 (0)438 516 702
www.tolven-example.com

Font styles to use
Other font styles liked:
• Please use font as close to corporate logo as possible

Colors
0255a3
0393ce
00a990
33b8a4
33a6d7
3176b5

Requirements
Must have
• Please include the words;
• Mobile Travel Management
• Accelerating Travel Business Insights
• Use corporate logo - although icon can be stylised if needed

```html
<!DOCTYPE html>
<html lang="en">
<head>
<meta charset="utf-8">
<title>tolvEn business card</title>
<link rel="stylesheet" href="https://fonts.googleapis.com/css2?family=Open+Sans:wght@400;600&display=swap">
<style>
  :root {
    --page: #d9d9d9;
    --card-light: #eef2f8;
    --card-dark: #393939;
    --brand-blue: #1aa7e6;
    --brand-slate: #45595a;
    --ink: #1c1c1c;
    --rule: #5b5b5b;
    --white: #fbf8f8;
  }
  * { margin: 0; padding: 0; box-sizing: border-box; }
  html, body {
    width: 1189px; height: 1200px; overflow: hidden;
    background: var(--page);
    font-family: "Open Sans", Arial, sans-serif;
  }
  .card {
    position: absolute; left: 140px; width: 917px; height: 522px;
    box-shadow: 0 4px 10px rgba(0,0,0,.35);
    overflow: hidden;
  }
  .card--front { top: 46px; background: var(--card-light); }
  .card--back { top: 624px; background: var(--card-dark); }

  .brand { position: absolute; left: 0; width: 100%; text-align: center; }
  .brand__mark {
    display: block; margin: 0 auto; border-radius: 50%;
    border: 7px solid var(--brand-blue);
  }
  .brand__name { display: block; font-weight: 600; letter-spacing: 1px; line-height: 1; }

  .card--front .brand { top: 40px; }
  .card--front .brand__mark { width: 95px; height: 95px; }
  .card--front .brand__name { font-size: 118px; color: var(--brand-slate); margin-top: -6px; }

  .card--back .brand { top: 125px; }
  .card--back .brand__mark { width: 120px; height: 120px; border-width: 8px; }
  .card--back .brand__name { font-size: 140px; color: var(--white); margin-top: -10px; }

  .tagline {
    position: absolute; left: 0; top: 400px; width: 100%;
    text-align: center; color: var(--brand-blue);
    font-size: 22px; line-height: 34px; letter-spacing: .5px;
  }

  .person { position: absolute; left: 77px; top: 350px; }
  .person__name { font-size: 37px; color: var(--brand-blue); line-height: 1.15; }
  .person__title { font-size: 28px; color: var(--ink); line-height: 1.3; }

  .divider { position: absolute; left: 387px; top: 287px; width: 2px; height: 186px; background: var(--rule); }

  .contacts { position: absolute; left: 433px; top: 296px; list-style: none; }
  .contacts li {
    display: flex; align-items: center; height: 43px;
    font-size: 23px; color: var(--ink);
  }
  .contacts svg { width: 20px; height: 20px; margin-right: 24px; flex: none; }
</style>
</head>
<body>
  <section class="card card--front">
    <div class="brand">
      <span class="brand__mark"></span>
      <span class="brand__name">tolvEn</span>
    </div>
    <div class="person">
      <p class="person__name">Rosalind Mercer</p>
      <p class="person__title">Chief Executive</p>
    </div>
    <div class="divider"></div>
    <ul class="contacts">
      <li>
        <svg viewBox="0 0 20 20" aria-hidden="true"><rect width="20" height="20" fill="#1aa7e6"/><circle cx="10" cy="10" r="6" fill="none" stroke="#fff" stroke-width="1.6"/><path d="M4 10h12M10 4v12" stroke="#fff" stroke-width="1.2"/></svg>
        www.tolven-example.com
      </li>
      <li>
        <svg viewBox="0 0 20 20" aria-hidden="true"><rect width="20" height="20" fill="#1aa7e6"/><path d="M7 4l2 3-1.5 1.5c.8 1.8 2.2 3.2 4 4L13 11l3 2-1.5 3C9 15 5 11 4 5.5z" fill="#fff"/></svg>
        +61 (0)2 8134 2907
      </li>
      <li>
        <svg viewBox="0 0 20 20" aria-hidden="true"><rect width="20" height="20" fill="#1aa7e6"/><rect x="6" y="3" width="8" height="14" rx="1.5" fill="none" stroke="#fff" stroke-width="1.5"/><rect x="8" y="5" width="4" height="5" fill="#fff"/></svg>
        +61 (0)438 516 702
      </li>
      <li>
        <svg viewBox="0 0 20 20" aria-hidden="true"><rect width="20" height="20" fill="#1aa7e6"/><rect x="3" y="5" width="14" height="10" fill="none" stroke="#fff" stroke-width="1.5"/><path d="M3 5l7 6 7-6" fill="none" stroke="#fff" stroke-width="1.5"/></svg>
        rosalind.mercer@tolven-example.com
      </li>
    </ul>
  </section>

  <section class="card card--back">
    <div class="brand">
      <span class="brand__mark"></span>
      <span class="brand__name">tolvEn</span>
    </div>
    <div class="tagline">
      <p>Mobile Travel Management</p>
      <p>Accelerating Travel Business Insights</p>
    </div>
  </section>
</body>
</html>
```